A4 Single Sided Brochure Folder Design Technical Company

We are a technical company based in the UK, working worldwide for Power Distribution companies.

We have technical literature and need a folder to present these in. The design should be very simple and clean using our logo and "Innovative Utility Solutions"

Our website kestrome.com gives and idea of the business but don't follow the look of the website as we will be redoing shortly.

• Logo and Strap Line
• Clean, easy to print and timeless
• Shouldn't be fashionable, we certainly aren't

```html
<!DOCTYPE html>
<html lang="en">
<head>
<meta charset="UTF-8">
<title>Kestrome – Brochure Folder</title>
<link rel="stylesheet" href="https://fonts.googleapis.com/css2?family=Lato:wght@300;400&display=swap">
<style>
  :root {
    --backdrop: #e4e4e4;
    --paper: #ffffff;
    --paper-back: #f7f7f7;
    --brand: #b0308f;
    --brand-light: #c95aa8;
    --strap: #b5b5b5;
    --url: #6a6a6a;
    --fold-shadow: rgba(0,0,0,0.08);
  }
  * { box-sizing: border-box; margin: 0; padding: 0; }
  html, body {
    width: 1200px; height: 750px; overflow: hidden;
    background: var(--backdrop);
    font-family: "Lato", Arial, sans-serif;
  }
  .folder-spread {
    position: absolute;
    left: 148px; top: 52px;
    width: 904px; height: 646px;
    display: flex;
    box-shadow: 0 10px 30px rgba(0,0,0,0.12);
  }
  .panel {
    position: relative;
    width: 452px; height: 646px;
    background: var(--paper);
  }
  .panel--back {
    background: linear-gradient(90deg, var(--paper) 0%, var(--paper-back) 85%, #eeeeee 100%);
  }
  .panel--front {
    box-shadow: inset 6px 0 10px -6px var(--fold-shadow);
  }
  .brand-rule {
    position: absolute;
    left: 0; right: 0; bottom: 26px;
    height: 5px;
    background: linear-gradient(90deg, var(--brand) 0%, var(--brand-light) 50%, var(--brand) 100%);
  }
  .web-address {
    position: absolute;
    left: 0; right: 0; bottom: 86px;
    text-align: center;
    font-size: 11px;
    font-weight: 400;
    letter-spacing: 0.5px;
    color: var(--url);
  }
  .brand-block {
    position: absolute;
    left: 0; right: 0; top: 250px;
    text-align: center;
  }
  .brand-name {
    font-size: 60px;
    font-weight: 400;
    letter-spacing: 1px;
    color: var(--brand);
    line-height: 1;
  }
  .strapline {
    margin-top: 10px;
    font-size: 19px;
    font-weight: 300;
    letter-spacing: 0.3px;
    color: var(--strap);
  }
</style>
</head>
<body>
  <main class="folder-spread">
    <section class="panel panel--back">
      <p class="web-address">www.kestrome.com</p>
      <div class="brand-rule"></div>
    </section>
    <section class="panel panel--front">
      <div class="brand-block">
        <h1 class="brand-name">Kestrome</h1>
        <p class="strapline">Innovative Utility Solutions</p>
      </div>
      <div class="brand-rule"></div>
    </section>
  </main>
</body>
</html>
```